2 Fold Brochure

We are a spa looking to create a professional elegant two fold brochure for a spa mainly black and white with a splash of lime green.
Look and feel: chic, modern, and spa-ish.

The front will include an image and also it should say: (somewhere under the photo) wherever you think it will look nice.
Skin Tightening
Cellulite Reduction
Body Contouring

The second Page:
Bipolar Radiofrequency(bolded): for immediate face lifting, tone and a complete new younger looking skin!
Multipolar Radiofrequency(bolded): with Vacuum system for body contour, cellulite and fat detachment from adipose tissue.
Cavitation with red LED to treat face and small areas of the body. Red LED light stimulates collagen synthesis.

Ultra Cavitation will sculpt, treat fat, cellulite and improve body shape! It does NOT involve surgery. There is no need for anesthesia, hospital stay or time off from work. Ultra cavitation will promote microscopic air bubbles to surround the lipocyte(fat cell) membranes and with its resonant frequency, the bubbles cause a high enough pressure to break up fat instantly. These broken lipocytes are then safely metabolized out of the human body.

PRESSOTHERAPY: A Complete Body Detox! Pressortherapy based on air pressure, promotes lymphatic drainage. It aslo has infrared system for body heat and electro muscle stimulation system.

Third Page:
Packages:

1. THE NEW FACELIFT:
*Skin Tightening
*Wrinkle Reduction
*Dark Circle Elimination
*Puffy Eye Relief

BODY SHAPING

2. BODY
*Fat Reduction
*Cellulite Reduction
*Body Firming

3. PRESSOTHERAPY (DETOX) $85
*Toxic Flushing
*Lymphatic Drainage
*Toning

5.POST PREGNANCY
*Fat Reduction
*Tummy Firming and Toning
*Cellulite Reduction
*Butt Toning

Buy 5 get 1 Free - $1,250
Buy 10 get 2 Free- $2,500

The back of the second page will include before and after photos I will be sending later. Also include the Logo in the front and by the prices. I have attached our logo.

Also we need a photo to place in the front. Something that shows face and body fat reduction.

Industry/Entity Type

Hospital

```html
<!DOCTYPE html>
<html lang="en">
<head>
<meta charset="utf-8">
<title>Verde Day Spa – Two Fold Brochure</title>
<link href="https://fonts.googleapis.com/css2?family=Raleway:wght@400;500;600;700&display=swap" rel="stylesheet">
<style>
:root{
  --lime:#8cc63f;
  --green:#3f9a1c;
  --deep-green:#2f7d12;
  --black:#0d0d0d;
  --ink:#222;
  --grey-text:#777;
  --soft-grey:#e9e9e9;
  --paper:#ffffff;
  --backdrop:#eeeeee;
  --orange:#f39200;
}
*{box-sizing:border-box;margin:0;padding:0}
html,body{width:1200px;height:1000px;overflow:hidden}
body{background:var(--backdrop);font-family:"Raleway",sans-serif;color:var(--ink);position:relative}
.spread{position:absolute;left:140px;width:920px;height:470px;display:flex;box-shadow:0 8px 24px rgba(0,0,0,.12)}
.spread--outer{top:15px}
.spread--inner{top:510px}
.page{position:relative;width:460px;height:470px;background:var(--paper);overflow:hidden}
.photo{position:absolute;display:block}
.brand{display:flex;align-items:center;gap:8px;font-weight:700;color:var(--ink);font-size:20px}
.brand__dot{width:14px;height:14px;border-radius:50%;background:var(--black);flex:none}
.svg-layer{position:absolute;inset:0}

/* page 1 cover */
.cover__band{position:absolute;left:0;top:0;width:460px;height:150px;background:linear-gradient(135deg,#4aa521,var(--deep-green))}
.cover__edge{position:absolute;left:0;top:0;width:26px;height:150px;background:var(--lime)}
.cover__headline{position:absolute;right:20px;top:26px;color:#fff;font-size:17px;line-height:1.45;text-align:left;width:260px}
.cover__headline strong{font-size:23px;font-weight:600}
.cover__headline .l2{padding-left:0}
.cover__headline .l3{padding-left:60px}
.cover__brand{position:absolute;left:24px;top:230px}
.cover__photo{left:200px;top:175px;width:260px;height:295px;background:linear-gradient(160deg,#f3e6d8,#c98a5c 55%,#a8683e)}
.cover__still{left:10px;top:380px;width:150px;height:80px;background:linear-gradient(135deg,#f4d7e0,#e9e2d0 60%,#b8c79a);border-radius:6px}

/* page 4 back */
.back__photo{left:0;top:0;width:320px;height:200px;background:linear-gradient(150deg,#cfd3d6,#efe4d6 50%,#c9a88c)}
.back__brand{position:absolute;left:22px;top:245px}
.back__prices{position:absolute;left:120px;top:220px;width:200px;background:#fff;padding:10px 14px;font-size:13px;line-height:1.9}
.back__prices span{color:var(--green);font-weight:600}
.back__strip{position:absolute;left:0;top:350px;width:460px;height:120px;background:var(--black)}
.back__ba{top:362px;height:96px;background:linear-gradient(135deg,#c9a487,#e7d3c0)}

/* page 2 */
.stripe{position:absolute;top:0;height:470px}
.stripe--black{left:0;width:22px;background:var(--black)}
.stripe--lime{left:22px;width:34px;background:var(--lime)}
.inner__photos{position:absolute;left:70px;top:0;width:390px;height:90px;display:flex;gap:4px}
.inner__photos .photo{position:static;flex:1;background:linear-gradient(135deg,#d8b08e,#b68160)}
.treatments{position:absolute;left:75px;top:100px;width:370px}
.treatment{margin-bottom:14px}
.treatment__title{font-size:13px;font-weight:600;color:var(--ink);letter-spacing:.5px;border-left:3px solid var(--green);padding-left:7px;line-height:1.2}
.treatment__title b{display:block;color:var(--green);font-size:15px;font-weight:700}
.treatment__title.single{color:var(--green);font-size:15px;font-weight:700}
.treatment p{font-size:9.5px;color:var(--grey-text);line-height:1.55;margin-top:5px}

/* page 3 */
.stripe--page3{left:0;width:30px;background:var(--lime)}
.corner{position:absolute;right:0;bottom:0}
.package{position:absolute;left:40px;width:410px;height:100px}
.package__thumb{position:absolute;top:4px;width:88px;height:88px;border-radius:50%;border:4px solid var(--lime)}
.package__text{position:absolute;top:6px}
.package__title{font-size:15px;font-weight:500}
.package__title strong{color:var(--green);font-weight:600;font-size:17px}
.package__list{list-style:none;font-size:9.5px;color:var(--grey-text);line-height:1.55;margin-top:4px}
.package__arrow{position:absolute;top:32px;width:22px;height:22px}
.offers{position:absolute;left:80px;top:420px;font-size:11px;font-weight:700;line-height:1.5}
.offers .buy{color:var(--orange)}
.offers .free{color:var(--green)}
</style>
</head>
<body>

<section class="spread spread--outer">
  <!-- Page 4: back -->
  <article class="page page--back">
    <div class="photo back__photo" role="img" aria-label="Therapist treating a client on a spa bed with a body contouring machine"></div>
    <svg class="svg-layer" viewBox="0 0 460 470" aria-hidden="true">
      <path d="M300 0 H460 V350 H430 C430 200 400 90 300 0Z" fill="var(--black)"/>
      <path d="M300 0 C380 60 420 150 430 260" stroke="var(--lime)" stroke-width="10" fill="none"/>
      <rect x="0" y="200" width="430" height="150" fill="#f3f3ef"/>
    </svg>
    <div class="brand back__brand"><span class="brand__dot"></span></div>
    <div class="back__prices">
      <div>The New Facelift - <span>$109</span></div>
      <div>Body Shaping - <span>$220</span></div>
      <div>The New Facelift - <span>$100</span></div>
      <div>The New Facelift - <span>$300</span></div>
    </div>
    <div class="back__strip"></div>
    <div class="photo back__ba" style="left:12px;width:140px" role="img" aria-label="Before and after photo of a waistline"></div>
    <div class="photo back__ba" style="left:158px;width:140px" role="img" aria-label="Before and after photo of a tummy"></div>
    <div class="photo back__ba" style="left:304px;width:144px;background:linear-gradient(135deg,#e8d2c2,#f6efe9)" role="img" aria-label="Before and after photo of cellulite reduction"></div>
  </article>

  <!-- Page 1: front cover -->
  <article class="page page--cover">
    <div class="cover__band"></div>
    <div class="cover__edge"></div>
    <div class="cover__headline">
      <div>Skin <strong>Tightening</strong></div>
      <div class="l2">Cellulite <strong>Reduction</strong></div>
      <div class="l3"><strong>Body</strong> Contouring</div>
    </div>
    <svg class="svg-layer" viewBox="0 0 460 470" aria-hidden="true">
      <path d="M0 150 H460 V170 C330 130 160 150 0 240Z" fill="var(--black)"/>
      <path d="M30 205 C170 150 330 140 460 172" stroke="var(--lime)" stroke-width="6" fill="none"/>
      <path d="M0 240 C160 150 330 130 460 170" stroke="var(--lime)" stroke-width="4" fill="none"/>
    </svg>
    <div class="photo cover__photo" role="img" aria-label="Woman holding a body contouring device to her hip"></div>
    <div class="photo cover__still" role="img" aria-label="Spa still life with flowers, towels and stones"></div>
    <div class="brand cover__brand"><span class="brand__dot"></span>Verde Day Spa</div>
  </article>
</section>

<section class="spread spread--inner">
  <!-- Page 2 -->
  <article class="page page--treatments">
    <div class="stripe stripe--black"></div>
    <div class="stripe stripe--lime"></div>
    <div class="inner__photos">
      <div class="photo" role="img" aria-label="Radiofrequency treatment on skin"></div>
      <div class="photo" role="img" aria-label="Before treatment photo"></div>
      <div class="photo" role="img" aria-label="After treatment photo"></div>
    </div>
    <div class="treatments">
      <div class="treatment">
        <h3 class="treatment__title">BIPOLAR<b>RADIOFREQUENCY</b></h3>
        <p>for immediate face lifting, tone and a complete new younger looking skin!</p>
      </div>
      <div class="treatment">
        <h3 class="treatment__title">MULTIPOLAR<b>RADIOFREQUENCY</b></h3>
        <p>with Vacuum system for body contour, cellulite and fat detachment from adipose tissue.<br>Cavitation with red LED to treat face and small areas of the body. Red LED light stimulates collagen synthesis.</p>
        <p>Ultra Cavitation will sculpt, treat fat, cellulite and improve body shape! It does NOT involve surgery. There is no need for anesthesia, hospital stay or time off from work. Ultra cavitation will promote microscopic air bubbles to surround the lipocyte (fat cell) membranes and with its resonant frequency, the bubbles cause a high enough pressure to break up fat instantly. These broken lipocytes are then safely metabolized out of the human body.</p>
      </div>
      <div class="treatment">
        <h3 class="treatment__title single">PRESSOTHERAPY</h3>
        <p>A Complete Body Detox! Pressotherapy based on air pressure, promotes lymphatic drainage. It also has infrared system for body heat and electro muscle stimulation system.</p>
      </div>
    </div>
  </article>

  <!-- Page 3 -->
  <article class="page page--packages">
    <div class="stripe stripe--page3"></div>
    <svg class="corner" width="200" height="200" viewBox="0 0 200 200" aria-hidden="true">
      <path d="M200 0 C180 90 120 160 20 200 H200Z" fill="var(--soft-grey)"/>
    </svg>

    <div class="package" style="top:20px">
      <div class="photo package__thumb" style="left:0;background:linear-gradient(135deg,#f2e2d4,#d9b89b)" role="img" aria-label="Woman relaxing after a facial"></div>
      <svg class="package__arrow" style="left:100px" viewBox="0 0 22 22" aria-hidden="true"><path d="M3 4 V13 H15 M11 8 L16 13 L11 18" stroke="var(--lime)" stroke-width="3" fill="none"/></svg>
      <div class="package__text" style="left:135px">
        <div class="package__title">The New <strong>Facelift</strong></div>
        <ul class="package__list"><li>Skin Tightening</li><li>Wrinkle Reduction</li><li>Dark Circle Elimination</li><li>Puffy Eye Relief</li></ul>
      </div>
    </div>

    <div class="package" style="top:120px">
      <div class="package__text" style="left:10px">
        <div class="package__title">Body <strong>Shaping</strong></div>
        <ul class="package__list"><li>Fat Reduction</li><li>Cellulite Reduction</li><li>Body Firming</li></ul>
      </div>
      <svg class="package__arrow" style="left:150px;top:44px" viewBox="0 0 22 22" aria-hidden="true"><path d="M19 4 V13 H7 M11 8 L6 13 L11 18" stroke="var(--lime)" stroke-width="3" fill="none"/></svg>
      <div class="photo package__thumb" style="left:185px;background:linear-gradient(135deg,#f3eef2,#6b3a5e)" role="img" aria-label="Body shaping garments"></div>
    </div>

    <div class="package" style="top:220px">
      <div class="photo package__thumb" style="left:0;background:linear-gradient(135deg,#f6b24a,#6b9a2c)" role="img" aria-label="Fresh juices and fruit for detox"></div>
      <svg class="package__arrow" style="left:100px" viewBox="0 0 22 22" aria-hidden="true"><path d="M3 4 V13 H15 M11 8 L16 13 L11 18" stroke="var(--lime)" stroke-width="3" fill="none"/></svg>
      <div class="package__text" style="left:135px">
        <div class="package__title">Pressotherapy <strong>(Detox)</strong> $85</div>
        <ul class="package__list"><li>Toxic Flushing</li><li>Lymphatic Drainage</li><li>Toning</li></ul>
      </div>
    </div>

    <div class="package" style="top:315px">
      <div class="package__text" style="left:10px">
        <div class="package__title">Post <strong>Pregnancy</strong></div>
        <ul class="package__list"><li>Fat Reduction</li><li>Tummy Firming and Toning</li><li>Cellulite Reduction</li><li>Butt Toning</li></ul>
      </div>
      <svg class="package__arrow" style="left:180px" viewBox="0 0 22 22" aria-hidden="true"><path d="M19 4 V13 H7 M11 8 L6 13 L11 18" stroke="var(--lime)" stroke-width="3" fill="none"/></svg>
      <div class="photo package__thumb" style="left:215px;background:linear-gradient(135deg,#f1d4df,#d24f8c)" role="img" aria-label="Mother with her baby"></div>
    </div>

    <div class="offers" style="left:40px">
      <div><span class="buy">BUY</span> 5 GET 1 <span class="free">FREE</span> - $1,250</div>
      <div><span class="buy">BUY</span> 10 GET 2 <span class="free">FREE</span> - $2,500</div>
    </div>
  </article>
</section>

</body>
</html>
```